Parcelwise HQ letterhead and envelope

Design a formal (8.5x11) letterhead and envelope for sales outreach and legal matters. Using design input from https://www.parcelwisehq.example/ and the attached documents.

Industry/Entity Type

Software Service

Requirements
Must have
• These 4 hex colors are our official colors:
• #355c98 [blue]
• #1eb1a2 [teal]
• #fdba12 [gold]
• #f1653b [orange]
• So no other colors besides these should be used.

```html
<!DOCTYPE html>
<html lang="en">
<head>
<meta charset="utf-8">
<title>Parcelwise HQ Letterhead</title>
<link rel="stylesheet" href="https://fonts.googleapis.com/css2?family=Lato:wght@400;700&family=Kaushan+Script&display=swap">
<style>
  :root {
    --brand-blue: #355c98;
    --brand-teal: #1eb1a2;
    --ink: #3a3a3a;
    --muted: #6b6b6b;
    --paper: #ffffff;
    --backdrop: #e9eaec;
    --rule: #d6d6d6;
  }
  html, body {
    margin: 0;
    width: 1200px;
    height: 936px;
    overflow: hidden;
    background: var(--backdrop);
    font-family: "Lato", Arial, sans-serif;
  }
  .letterhead {
    position: absolute;
    left: 260px;
    top: 28px;
    width: 680px;
    height: 880px;
    background: var(--paper);
    box-shadow: 0 6px 22px rgba(0,0,0,0.12);
    overflow: hidden;
  }
  .letterhead__wave {
    position: absolute;
    left: 0;
    top: 0;
    width: 680px;
    height: 210px;
  }
  .brand {
    position: absolute;
    right: 48px;
    top: 58px;
    display: flex;
    align-items: center;
    gap: 10px;
  }
  .brand__dot {
    width: 26px;
    height: 26px;
    border: 3px solid var(--brand-blue);
    border-radius: 50%;
    box-sizing: border-box;
  }
  .brand__name {
    font-size: 30px;
    font-weight: 400;
    color: var(--brand-blue);
    letter-spacing: 0.5px;
  }
  .letter {
    position: absolute;
    left: 64px;
    top: 258px;
    width: 548px;
    font-size: 12.5px;
    line-height: 1.55;
    color: var(--ink);
  }
  .letter__salutation {
    margin: 0 0 6px;
    font-weight: 700;
    color: var(--brand-blue);
  }
  .letter__paragraph {
    margin: 0 0 16px;
    text-align: justify;
  }
  .letter__closing {
    margin: 34px 0 2px;
    font-size: 15px;
    color: var(--ink);
  }
  .letter__signature {
    margin: 0;
    font-family: "Kaushan Script", cursive;
    font-size: 26px;
    color: var(--brand-blue);
  }
  .contact-bar {
    position: absolute;
    left: 64px;
    right: 48px;
    bottom: 34px;
    display: flex;
    font-size: 11.5px;
    color: var(--muted);
  }
  .contact-bar__group {
    flex: 1;
    padding: 0 16px;
    border-left: 1px solid var(--rule);
  }
  .contact-bar__group:first-child {
    padding-left: 0;
    border-left: none;
  }
  .contact-bar__item {
    display: flex;
    align-items: center;
    gap: 6px;
    margin: 3px 0;
    white-space: nowrap;
  }
  .contact-bar__icon {
    width: 12px;
    height: 12px;
    flex: none;
  }
  .letterhead__base {
    position: absolute;
    left: 0;
    bottom: 0;
    width: 100%;
    height: 6px;
    background: var(--brand-blue);
  }
</style>
</head>
<body>
  <main class="letterhead">
    <svg class="letterhead__wave" viewBox="0 0 680 210" aria-hidden="true">
      <path d="M0 0 H680 V6 C500 14 250 60 0 176 Z" fill="var(--brand-blue)"/>
      <path d="M680 6 C500 14 250 60 0 176 V184 C250 74 480 38 680 30 Z" fill="var(--brand-teal)"/>
      <path d="M0 192 C250 82 480 46 680 36" fill="none" stroke="var(--brand-blue)" stroke-width="1.5"/>
    </svg>

    <div class="brand">
      <span class="brand__dot"></span>
      <span class="brand__name">Parcelwise HQ</span>
    </div>

    <section class="letter">
      <p class="letter__salutation">Dear Mr. Lorem,</p>
      <p class="letter__paragraph">Lorem ipsum dolor sit amet, consectetuer adipiscing elit, sed diam nonummy nibh euismod tincidunt ut laoreet dolore magna aliquam erat volutpat. Ut wisi enim ad minim veniam, quis nostrud exerci tation ullamcorper suscipit lobortis nisl ut aliquip ex ea commodo consequat. Duis autem vel eum iriure dolor in hendrerit odio dignissim qui blandit praesent luptatum zzril delenit augue duis dolore te feugait nulla facilisi.</p>
      <p class="letter__paragraph">Lorem ipsum dolor sit amet, consectetuer adipiscing elit, sed diam nonummy nibh euismod tincidunt ut laoreet dolore magna aliquam erat volutpat. Ut wisi enim ad minim veniam, quis nostrud exerci tation ullamcorper suscipit lobortis nisl ut aliquip ex ea commodo consequat. Duis autem vel eum iriure dolor in hendrerit odio dignissim qui blandit praesent luptatum zzril delenit augue duis dolore te feugait nulla facilisi.</p>
      <p class="letter__paragraph">Lorem ipsum dolor sit amet, consectetuer adipiscing elit, sed diam nonummy nibh euismod tincidunt ut laoreet dolore magna aliquam erat volutpat. Ut wisi enim ad minim veniam, quis nostrud exerci tation ullamcorper suscipit lobortis nisl ut aliquip ex ea commodo consequat. Duis autem vel eum iriure dolor in hendrerit odio dignissim qui blandit praesent luptatum zzril delenit augue duis dolore te feugait nulla facilisi.</p>
      <p class="letter__closing">Sincerely Your,</p>
      <p class="letter__signature">Your Name</p>
    </section>

    <footer class="contact-bar">
      <div class="contact-bar__group">
        <div class="contact-bar__item">
          <svg class="contact-bar__icon" viewBox="0 0 12 12"><circle cx="6" cy="6" r="5.5" fill="none" stroke="var(--brand-blue)"/><rect x="4" y="2.5" width="4" height="7" rx="0.8" fill="var(--brand-blue)"/></svg>
          (555) 010-4821
        </div>
        <div class="contact-bar__item">
          <svg class="contact-bar__icon" viewBox="0 0 12 12"><circle cx="6" cy="6" r="5.5" fill="none" stroke="var(--brand-blue)"/><path d="M3.5 3.5 L5 3 L5.8 4.8 L5 5.4 Q5.8 6.8 6.8 7.2 L7.4 6.4 L9 7.2 L8.6 8.6 Q5 8.6 3.5 3.5 Z" fill="var(--brand-blue)"/></svg>
          (555) 010-3073 (Main)
        </div>
      </div>
      <div class="contact-bar__group">
        <div class="contact-bar__item">
          <svg class="contact-bar__icon" viewBox="0 0 12 12"><circle cx="6" cy="6" r="5.5" fill="none" stroke="var(--brand-blue)"/><rect x="3" y="4" width="6" height="4.2" fill="none" stroke="var(--brand-blue)"/><path d="M3 4 L6 6.4 L9 4" fill="none" stroke="var(--brand-blue)"/></svg>
          jsmith@parcelwisehq.example
        </div>
        <div class="contact-bar__item">
          <svg class="contact-bar__icon" viewBox="0 0 12 12"><circle cx="6" cy="6" r="5.5" fill="none" stroke="var(--brand-blue)"/><circle cx="6" cy="6" r="3" fill="none" stroke="var(--brand-blue)"/><path d="M3 6 H9 M6 3 V9" stroke="var(--brand-blue)" stroke-width="0.8"/></svg>
          www.parcelwisehq.example
        </div>
      </div>
      <div class="contact-bar__group">
        <div class="contact-bar__item">
          <svg class="contact-bar__icon" viewBox="0 0 12 12"><circle cx="6" cy="6" r="5.5" fill="none" stroke="var(--brand-blue)"/><path d="M6 9.5 C4 7 3.8 5.8 3.8 5 A2.2 2.2 0 0 1 8.2 5 C8.2 5.8 8 7 6 9.5 Z" fill="var(--brand-blue)"/><circle cx="6" cy="5" r="0.8" fill="var(--paper)"/></svg>
          42 Harbor Lane
        </div>
        <div class="contact-bar__item" style="padding-left:18px">Springvale, MI 40000</div>
      </div>
    </footer>
    <div class="letterhead__base"></div>
  </main>
</body>
</html>
```